We have a company that provide sandblasted stone products. Example: numbers for houses. Also we sell cultured stone,brick natural stone to the contractor,homeowner. We need to get a business card that describe our product and service. In the original idea we had an old fashion chisel striking through the x in velquarin.

Reason: We realized that 2 days was not enough time for the competion to be open many of the designers may be to busy and require more time to compete.

Industry/Entity Type

It Company

Logo Text

Velquarin

```html
<!DOCTYPE html>
<html lang="en">
<head>
<meta charset="utf-8">
<title>Velquarin Business Card</title>
<link href="https://fonts.googleapis.com/css2?family=Arimo:wght@400;700&family=Tinos:wght@400&display=swap" rel="stylesheet">
<style>
  :root {
    --orange: #ec6a1f;
    --orange-soft: #f4a57a;
    --white: #ffffff;
    --ink: #1c1c1c;
    --ink-grey: #4a4a4a;
    --name-grey: #6b6b6b;
    --black-band: #111111;
    --backdrop: #e9e6e2;
  }
  html, body {
    margin: 0;
    padding: 0;
    width: 1200px;
    height: 900px;
    overflow: hidden;
    background: var(--backdrop);
  }
  .canvas {
    position: relative;
    width: 1200px;
    height: 900px;
    display: flex;
    align-items: center;
    justify-content: center;
    gap: 40px;
  }
  .card {
    position: relative;
    width: 560px;
    height: 320px;
    box-shadow: 0 6px 18px rgba(0,0,0,0.18);
    overflow: hidden;
  }

  /* Front */
  .card-front {
    background: linear-gradient(150deg, var(--orange) 0%, var(--orange-soft) 45%, var(--white) 95%);
  }
  .brand {
    position: absolute;
    left: 120px;
    top: 130px;
    display: flex;
    align-items: center;
    gap: 14px;
  }
  .brand-dot {
    width: 34px;
    height: 34px;
    border-radius: 50%;
    background: var(--orange);
  }
  .brand-name {
    font-family: "Tinos", "Times New Roman", serif;
    font-size: 46px;
    font-weight: 400;
    letter-spacing: 1px;
    color: var(--ink);
  }

  /* Back */
  .card-back {
    background: var(--white);
  }
  .edge-band {
    position: absolute;
    left: 0;
    top: 0;
    width: 10px;
    height: 100%;
    background: linear-gradient(to bottom, var(--black-band) 0%, var(--black-band) 58%, var(--orange) 58%, var(--orange) 100%);
  }
  .contact {
    position: absolute;
    left: 40px;
    top: 30px;
    font-family: "Arimo", Arial, sans-serif;
    color: var(--ink-grey);
    font-size: 14px;
    line-height: 1.35;
  }
  .contact-name {
    font-size: 22px;
    font-weight: 700;
    color: var(--name-grey);
    margin: 0;
  }
  .contact-title {
    font-size: 14px;
    margin: 0 0 14px;
  }
  .contact-lines {
    margin: 0;
    padding: 0;
    list-style: none;
  }
</style>
</head>
<body>
  <main class="canvas">
    <section class="card card-front" aria-label="Card front">
      <div class="brand">
        <span class="brand-dot"></span>
        <span class="brand-name">VELQUARIN</span>
      </div>
    </section>

    <section class="card card-back" aria-label="Card back">
      <div class="edge-band"></div>
      <div class="contact">
        <p class="contact-name">Alex Marlow</p>
        <p class="contact-title">Chief Executive Officer</p>
        <ul class="contact-lines">
          <li>Unit 12</li>
          <li>48 Quarry Lane, Canada</li>
          <li>Tel: 555 0142</li>
          <li>Mob: 555 0198</li>
          <li>Email: alex@velquarin.com</li>
          <li>www.velquarin.com</li>
        </ul>
      </div>
    </section>
  </main>
</body>
</html>
```